Business Card Design

New business card design

Target Market(s)

Residential & Commercial Property Managers

Industry/Entity Type

Plumbing Services

Contact Information for Business Card

Name - Rowan Keddle, title - Director, Phone Number - 0431 286 517, email - rowan@tbk-plumbing.com.au, Company ABN - 73 215 904 386,

Font styles to use
Sans Serif

Colors
0054AA
0677BA
7BADD7
CADEEF
E8F1F8

```html
<!DOCTYPE html>
<html lang="en">
<head>
<meta charset="utf-8">
<title>TBK Plumbing Services – Business Card</title>
<link rel="stylesheet" href="https://fonts.googleapis.com/css2?family=Montserrat:wght@400;500;700&display=swap">
<style>
  :root {
    --page-bg: #e4e2e3;
    --card-white: #ffffff;
    --ink: #1f2530;
    --brand-blue: #2ba8e0;
    --muted: #3a3f47;
  }
  * { box-sizing: border-box; margin: 0; padding: 0; }
  html, body {
    width: 1200px;
    height: 1108px;
    overflow: hidden;
    background: var(--page-bg);
    font-family: "Montserrat", Arial, sans-serif;
    color: var(--ink);
  }
  .canvas { position: relative; width: 1200px; height: 1108px; }

  .card {
    position: absolute;
    left: 236px;
    width: 740px;
    overflow: hidden;
  }
  .card--front { top: 61px; height: 446px; background: var(--card-white); }
  .card--back  { top: 580px; height: 441px; background: var(--brand-blue); }

  .brand {
    position: absolute;
    display: flex;
    align-items: center;
    gap: 10px;
    font-weight: 500;
    color: var(--ink);
    white-space: nowrap;
  }
  .brand__dot {
    display: inline-block;
    border-radius: 50%;
    background: var(--brand-blue);
  }
  .card--front .brand {
    left: 60px; top: 218px;
    font-size: 21px;
  }
  .card--front .brand__dot { width: 14px; height: 14px; }

  .card--back .brand {
    left: 0; right: 0; top: 190px;
    justify-content: center;
    font-size: 48px;
    gap: 18px;
  }
  .card--back .brand__dot { width: 30px; height: 30px; background: var(--card-white); }

  .divider {
    position: absolute;
    left: 373px; top: 150px;
    width: 2px; height: 185px;
    background: var(--ink);
  }

  .contact {
    position: absolute;
    left: 393px; top: 148px;
  }
  .contact__name { font-size: 27px; font-weight: 700; line-height: 1.2; }
  .contact__title { font-size: 16px; font-weight: 500; margin-top: 1px; }
  .contact__list { list-style: none; margin-top: 20px; }
  .contact__item {
    display: flex; align-items: center; gap: 11px;
    font-size: 16px; line-height: 1; height: 31px;
  }
  .contact__icon { width: 16px; height: 16px; fill: var(--ink); flex: none; }
  .contact__abn { font-size: 16px; margin-top: 1px; }
  .contact__abn strong { font-weight: 700; }

  .card__band { position: absolute; left: 0; bottom: 0; width: 740px; height: 25px; }
</style>
</head>
<body>
<main class="canvas">

  <section class="card card--front" aria-label="Business card front">
    <div class="brand"><span class="brand__dot"></span>TBK Plumbing Services</div>
    <div class="divider"></div>
    <div class="contact">
      <h1 class="contact__name">Rowan Keddle</h1>
      <p class="contact__title">Director</p>
      <ul class="contact__list">
        <li class="contact__item">
          <svg class="contact__icon" viewBox="0 0 24 24" aria-hidden="true"><path d="M6.6 10.8a15.1 15.1 0 0 0 6.6 6.6l2.2-2.2a1 1 0 0 1 1-.25 11.4 11.4 0 0 0 3.6.57 1 1 0 0 1 1 1V20a1 1 0 0 1-1 1A17 17 0 0 1 3 4a1 1 0 0 1 1-1h3.5a1 1 0 0 1 1 1c0 1.25.2 2.45.57 3.57a1 1 0 0 1-.25 1z"/></svg>
          0431 286 517
        </li>
        <li class="contact__item">
          <svg class="contact__icon" viewBox="0 0 24 24" aria-hidden="true"><path d="M3 6h18v1.2l-9 6-9-6zM3 9.2l9 6 9-6V18H3z"/></svg>
          rowan@tbk-plumbing.com.au
        </li>
        <li class="contact__item">
          <svg class="contact__icon" viewBox="0 0 24 24" aria-hidden="true"><circle cx="12" cy="12" r="9"/><path d="M12 3v18M3 12h18" stroke="#fff" stroke-width="1.4" fill="none"/></svg>
          www.tbk-plumbing.com.au
        </li>
      </ul>
      <p class="contact__abn"><strong>ABN</strong> - 73 215 904 386,</p>
    </div>
    <svg class="card__band" viewBox="0 0 740 25" preserveAspectRatio="none" aria-hidden="true">
      <polygon points="0,0 370,0 353,25 0,25" fill="var(--ink)"/>
      <polygon points="386,0 740,0 740,25 369,25" fill="var(--brand-blue)"/>
    </svg>
  </section>

  <section class="card card--back" aria-label="Business card back">
    <div class="brand"><span class="brand__dot"></span>TBK Plumbing Services</div>
  </section>

</main>
</body>
</html>
```